Flat Belly Design Graphics for Social

I want to create 9 social media graphics (new Instagram size 4:5 (1080 x 1350 pixels) focusing on our Flat Belly Graphics, using the pics attached. Use the attached pics, NO RANDOM STOCK PHOTOGRAPHY. For the color scheme of the graphics, the color palette is attached. YOU MUST POST ALL 9 GRAPHICS IN ONE ENTRY.
Using the 3 titles below, create one set of graphics. 1) with all text, then for the others, use the pictures as detailed below in IMPORTANT:
1. Ten-Week Bright Morning Reboot
2. The Quick Garden Kitchen Menu Guide
3. Studio Habits for Lasting Energy Past Midlife - Zero Gym Needed
IMPORTANT:
Only use RK Pic 1 and RK Pic 2 with the title, Ten-Week Bright Morning Reboot
Only use meal plan1 and meal plan2 pics with the title, Quick Garden Kitchen Menu Guide
Only use studio habits 1 and studio habits 2 pics with the title, Studio Habits for Lasting Energy Past Midlife - Zero Gym Needed
women over 40

```html
<!DOCTYPE html>
<html lang="en">
<head>
<meta charset="utf-8">
<title>Bright Morning Social Set</title>
<link rel="stylesheet" href="https://fonts.googleapis.com/css2?family=Oswald:wght@600;700&display=swap">
<style>
  :root{
    --ink:#2d4a45;
    --pink:#e295ab;
    --pink-deep:#c9587d;
    --blush:#f6d9e1;
    --white:#ffffff;
    --sky:#86cfe2;
    --forest:#2f6b45;
    --teal:#5f9e98;
    --wine:#8a3f5c;
    --night:#1f2f2c;
  }
  *{box-sizing:border-box;margin:0;padding:0}
  html,body{width:1200px;height:984px;overflow:hidden;background:var(--white)}
  body{position:relative;font-family:"Oswald",sans-serif;font-weight:700;text-transform:uppercase}
  .tile{position:absolute;width:381px;height:476px;overflow:hidden}
  .col-1{left:12px}.col-2{left:409px}.col-3{left:806px}
  .row-1{top:9px}.row-2{top:495px}
  .line{position:absolute;left:0;right:0;text-align:center;line-height:1;white-space:nowrap}
  .left{text-align:left;left:18px}

  /* Tile: studio habits, all text */
  .habits-text{background:linear-gradient(160deg,var(--forest) 0%,var(--teal) 35%,#4f8f7a 60%,#225a38 100%)}
  .ribbon{position:absolute;height:50px;background:var(--pink);box-shadow:0 6px 0 var(--pink-deep);transform:skewY(-12deg);display:flex;align-items:center;justify-content:center}
  .ribbon span{display:block;transform:skewY(12deg) rotate(-12deg);color:var(--blush);font-size:44px;line-height:1}
  .ribbon-a{left:84px;width:270px;top:38px}
  .ribbon-b{left:44px;width:232px;top:104px}
  .habits-text .sm{color:var(--white);font-size:38px}
  .habits-text .big{color:var(--blush);font-size:74px}

  /* Tile: kitchen menu with food */
  .satin{background:linear-gradient(180deg,#c96b8c 0%,#a45070 22%,#4a3440 52%,var(--night) 100%)}
  .menu-head{color:var(--white);font-size:40px}
  .menu-foot{color:var(--white);font-size:58px}
  .band{position:absolute;left:0;width:381px;height:76px}
  .band-word{color:var(--ink);font-size:82px}
  .food-arch{position:absolute;left:-38px;top:208px;width:456px;height:456px;border-radius:50%;border:6px solid var(--white);background:radial-gradient(circle at 50% 40%,#7a4e36 0%,#5a3a2a 55%,#3f2a20 100%)}

  /* Tile: studio habits with photo */
  .habits-photo{background:var(--sky)}
  .people-photo{position:absolute;left:150px;top:0;width:231px;height:476px;background:linear-gradient(180deg,#9ad7e7 0%,#c99a86 30%,#e2b9b4 55%,#b8cfe0 85%,#8fb3cf 100%);border-radius:120px 0 0 0}
  .habits-photo .ink{color:var(--ink)}
  .slant-band{position:absolute;left:0;top:305px;width:160px;height:122px}
  .habits-photo .band-text{color:var(--blush);font-size:32px}

  /* Tile: morning reboot with person */
  .reboot-photo{background:linear-gradient(150deg,var(--pink) 0%,#eab0c1 45%,var(--pink) 100%)}
  .reboot-photo .shade{position:absolute;left:0;top:0}
  .person-photo{position:absolute;left:124px;top:80px;width:257px;height:396px;border-radius:110px 110px 0 0;background:linear-gradient(180deg,#2a2022 0%,#6e4a3c 28%,#f1eeee 45%,#eae6e6 62%,#6b4a3b 75%,#1c1a1b 100%)}
  .shadowed{color:var(--white);text-shadow:3px 3px 0 var(--pink-deep)}
  .reboot-photo .head{font-size:56px}
  .reboot-photo .tail{color:var(--white);font-size:54px}

  /* Tile: morning reboot, all text */
  .reboot-text{background:radial-gradient(circle at 50% 50%,#fff6f7 0%,#fbe3e5 55%,#f4c9cc 100%)}
  .reboot-text .ink{color:var(--ink)}
  .reboot-text .pinkword{color:var(--pink);text-shadow:4px 4px 0 var(--pink-deep);font-size:92px}
</style>
</head>
<body>

<!-- Tile 1 -->
<section class="tile col-1 row-1 habits-text">
  <div class="ribbon ribbon-a"><span>Studio</span></div>
  <div class="ribbon ribbon-b"><span>Habits</span></div>
  <p class="line sm" style="top:162px">For Lasting</p>
  <p class="line big" style="top:206px">Energy</p>
  <p class="line sm" style="top:290px">Past Midlife</p>
  <p class="line big" style="top:340px;font-size:62px;color:var(--blush)">Zero Gym</p>
  <p class="line big" style="top:400px;font-size:62px;color:var(--blush)">Needed</p>
</section>

<!-- Tile 2 -->
<section class="tile col-2 row-1 satin">
  <p class="line menu-head" style="top:14px">The Quick Garden</p>
  <svg class="band" style="top:64px" viewBox="0 0 381 76" aria-hidden="true">
    <polygon points="0,0 381,0 352,38 381,76 0,76 29,38" fill="var(--blush)"/>
  </svg>
  <p class="line band-word" style="top:62px">Kitchen</p>
  <p class="line menu-foot" style="top:144px">Menu Guide</p>
  <div class="food-arch" role="img" aria-label="Overhead photo of healthy ingredients and a written menu plan on a wooden table"></div>
</section>

<!-- Tile 3 -->
<section class="tile col-3 row-1 habits-photo">
  <div class="people-photo" role="img" aria-label="Photo of two women sharing a surprised whisper"></div>
  <p class="line left ink" style="top:48px;font-size:42px">Studio</p>
  <p class="line left ink" style="top:92px;font-size:42px">Habits</p>
  <p class="line left ink" style="top:139px;font-size:30px">For Lasting</p>
  <p class="line left ink" style="top:176px;font-size:40px">Energy</p>
  <p class="line left ink" style="top:222px;font-size:40px">Past</p>
  <p class="line left ink" style="top:266px;font-size:32px">Midlife</p>
  <svg class="slant-band" viewBox="0 0 160 122" aria-hidden="true">
    <polygon points="0,0 152,0 140,61 160,122 0,122" fill="var(--pink)"/>
  </svg>
  <p class="line left band-text" style="top:311px">Zero</p>
  <p class="line left band-text" style="top:351px">Gym</p>
  <p class="line left band-text" style="top:390px">Needed</p>
</section>

<!-- Tile 4 -->
<section class="tile col-1 row-2 reboot-photo">
  <svg class="shade" width="381" height="476" viewBox="0 0 381 476" aria-hidden="true">
    <polygon points="0,205 178,236 72,476 0,476" fill="var(--ink)"/>
  </svg>
  <div class="person-photo" role="img" aria-label="Photo of a smiling woman in a white cropped sweater pointing down"></div>
  <p class="line left shadowed head" style="top:26px">Ten-Week</p>
  <p class="line left shadowed head" style="top:88px">Bright</p>
  <p class="line left shadowed head" style="top:150px">Morning</p>
  <p class="line left tail" style="top:268px">Re</p>
  <p class="line left tail" style="top:330px">boot</p>
  <svg style="position:absolute;left:100px;top:400px" width="100" height="70" viewBox="0 0 100 70" aria-hidden="true">
    <path d="M18 6 C2 30 14 58 62 52" fill="none" stroke="var(--pink)" stroke-width="10" stroke-linecap="round"/>
    <polygon points="58,36 92,50 60,68" fill="var(--pink)"/>
  </svg>
</section>

<!-- Tile 5 -->
<section class="tile col-2 row-2 reboot-text">
  <p class="line ink" style="top:22px;font-size:58px">Ten-Week</p>
  <p class="line pinkword" style="top:92px">Bright</p>
  <p class="line pinkword" style="top:196px">Morning</p>
  <p class="line ink" style="top:312px;font-size:78px">Reboot</p>
</section>

<!-- Tile 6 -->
<section class="tile col-3 row-2 satin">
  <p class="line menu-head" style="top:152px">The Quick Garden</p>
  <svg class="band" style="top:200px" viewBox="0 0 381 76" aria-hidden="true">
    <polygon points="0,0 381,0 352,38 381,76 0,76 29,38" fill="var(--blush)"/>
  </svg>
  <p class="line band-word" style="top:198px">Kitchen</p>
  <p class="line menu-foot" style="top:280px">Menu Guide</p>
</section>

</body>
</html>
```